Global Beard Oil Review Business needs a refresh

topwhiskertonic.net is a global business who's mission is to curate all available beard oils from around the world, review and grade them and present this curated collection to the user of the website.

The scope of this job includes the web site design and the design of a suitable logo to be used in the site header.

The existing site can be seen on http://topwhiskertonic.net, however this is a mock-up only the style and logo should NOT be used. This is to give you an idea of the concept of the site only.

This job is for PSD design only.

See attached design brief for detailed design requirements.
Updates

Project Deadline Extended
Reason: Extending deadline by 5 days to allow for final submissions

Target Market(s)

Men's grooming / retail

Industry/Entity Type

Retail

Number of Pages Required

2 page

Font styles to use
Sans Serif

Requirements
Must have
• 1) Comparison Table
• 2) Side Bar
• 3) Header area
• 4) Photo of Delvin Marsk (attached - can be circular or "cut-out")
• 5) Cool beard-oriented custom design background (e.g., stylistic black/brown on brown/orange beard background. I envision this beard background "drawing" rather than photo based)
• (see attached design requirements for details)
Nice to have
• Signature style writing at top with name "Delvin Marsk"
Should not have
• Do NOT use the look & feel or logo from the existing site.

```html
<!DOCTYPE html>
<html lang="en">
<head>
<meta charset="utf-8">
<title>Top Whisker Tonic</title>
<link href="https://fonts.googleapis.com/css2?family=Amatic+SC:wght@700&family=Raleway:wght@400;500;600;700&family=Mrs+Saint+Delafield&display=swap" rel="stylesheet">
<style>
:root{
  --orange:#f7a400;
  --maroon:#6b0a0a;
  --ink:#2b2b2b;
  --muted:#555;
  --line:#e4e4e4;
  --navbar:#ececec;
  --page:#d9d9d9;
  --white:#fff;
}
*{box-sizing:border-box;margin:0;padding:0}
html,body{width:1200px;height:2715px;overflow:hidden}
body{position:relative;font-family:"Raleway",Arial,sans-serif;color:var(--ink);background:var(--page)}
.display{font-family:"Amatic SC","Arial Narrow",sans-serif;font-weight:700}

/* header */
.site-header{position:absolute;left:0;top:0;width:1200px;height:127px;background:var(--white)}
.brand{position:absolute;left:76px;top:28px;display:flex;align-items:center;gap:12px}
.brand-dot{width:26px;height:26px;border-radius:50%;background:var(--orange)}
.brand-name{font-family:"Amatic SC",sans-serif;font-weight:700;font-size:40px;line-height:36px;color:var(--ink);width:150px}
.avatar{position:absolute;left:322px;top:4px;width:160px;height:160px;border-radius:50%;border:6px solid var(--white);background:radial-gradient(circle at 50% 40%,#8a8a8a,#3b3b3b);box-shadow:0 2px 6px rgba(0,0,0,.25);z-index:3}
.signature{position:absolute;left:486px;top:18px;font-family:"Mrs Saint Delafield",cursive;font-size:40px;line-height:50px;color:var(--ink);white-space:nowrap}
.contact{position:absolute;top:24px;display:flex;align-items:center;gap:8px;font-size:15px;color:var(--ink);white-space:nowrap}
.contact .ico{width:36px;height:36px;border-radius:50%;background:var(--orange);display:flex;align-items:center;justify-content:center;flex:none}
.contact-mail{left:716px}
.contact-phone{left:968px}
.main-nav{position:absolute;left:525px;top:85px;width:675px;height:40px;background:var(--navbar);display:flex;align-items:center;padding-left:12px;font-size:16px;font-weight:500}
.main-nav a{color:var(--ink);text-decoration:none;padding:4px 10px}
.main-nav a.active{background:var(--maroon);color:var(--white)}
.main-nav .sep{width:4px;height:4px;border-radius:50%;background:#777;margin:0 6px}

/* hero */
.hero{position:absolute;left:0;top:127px;width:1200px;height:488px;background:linear-gradient(100deg,#8c7a63 0%,#c9b89e 30%,#e6ddcf 60%,#efe9e0 100%)}
.hero-title{position:absolute;left:646px;top:110px;font-size:72px;line-height:92px;color:#3a2d22}
.hero-btn{position:absolute;left:646px;top:308px;width:143px;height:57px;background:var(--orange);color:var(--ink);font-size:24px;display:flex;align-items:center;justify-content:center}
.hero-arrow{position:absolute;top:190px}

/* background */
.page-backdrop{position:absolute;left:0;top:615px;width:1200px;height:2060px;background:linear-gradient(180deg,#dcdcdc,#cfcfcf)}

/* content */
.content{position:absolute;left:60px;top:615px;width:1080px;height:2060px;background:var(--white)}
.welcome-title{position:absolute;left:0;top:50px;width:1080px;text-align:center;font-size:66px;color:var(--maroon)}
.welcome-title span{color:var(--orange)}
.welcome-text{position:absolute;left:97px;top:143px;width:890px;text-align:center;font-size:13px;line-height:22px;color:var(--ink)}
.process{position:absolute;left:0;top:270px;width:1080px;height:200px}
.step{position:absolute;width:180px;text-align:center}
.step .circle{width:110px;height:110px;border-radius:50%;background:var(--orange);margin:0 auto;display:flex;align-items:center;justify-content:center}
.step .label{font-size:30px;margin-top:8px;color:var(--ink)}

/* comparison table */
.compare{position:absolute;left:20px;top:487px;width:738px;height:1519px;border:1px solid var(--line);border-radius:4px;background:var(--white)}
.compare-head{height:62px;background:var(--maroon);color:var(--white);position:relative;border-radius:3px 3px 0 0}
.compare-head h2{position:absolute;left:14px;top:6px;font-size:42px;color:var(--orange);font-weight:700}
.filter{position:absolute;top:12px;width:88px;font-size:12px;line-height:16px;border-bottom:1px solid rgba(255,255,255,.6);padding-bottom:2px;white-space:nowrap}
.filter b{color:var(--orange);font-weight:700;display:block}
.compare-row{position:relative;height:172px;border-bottom:1px solid var(--line)}
.thumb{position:absolute;left:14px;top:32px;width:100px;height:108px;border-radius:6px;background:linear-gradient(180deg,#efe9e2 0%,#a45a25 45%,#6d3512 100%)}
.product-name{position:absolute;left:132px;top:22px;font-size:22px;font-weight:700;color:var(--maroon);white-space:nowrap}
.product-maker{position:absolute;left:132px;top:57px;font-size:14px;color:var(--muted)}
.meta{position:absolute;font-size:11px;color:var(--ink);white-space:nowrap}
.meta b{color:var(--orange);font-weight:700}
.buy{position:absolute;left:613px;top:63px;width:105px;height:38px;background:var(--orange);color:var(--white);font-size:15px;display:flex;align-items:center;justify-content:center}
.loading{position:absolute;left:287px;top:1450px;width:169px;height:36px;background:#d6d6d6;color:var(--white);font-size:16px;display:flex;align-items:center;justify-content:center;gap:6px}

/* sidebar */
.newsletter{position:absolute;left:794px;top:487px;width:266px;height:341px;background:var(--orange);text-align:center;padding:18px 20px}
.newsletter h3{font-size:38px;line-height:44px;color:var(--maroon)}
.newsletter p{font-size:12px;line-height:17px;color:var(--ink);margin-top:10px}
.newsletter .field{height:36px;background:var(--white);margin-top:20px;font-size:11px;color:#999;display:flex;align-items:center;justify-content:center}
.newsletter .signup{height:36px;background:var(--maroon);color:var(--white);font-weight:700;font-size:13px;margin-top:14px;display:flex;align-items:center;justify-content:center}
.newsletter small{display:block;font-size:10px;line-height:14px;color:var(--white);margin-top:18px}
.blog-title{position:absolute;left:794px;top:870px;font-size:40px;color:var(--maroon)}
.post{position:absolute;left:794px;width:266px}
.post .pic{height:153px;border-radius:2px}
.post h4{font-size:16px;font-weight:700;color:var(--orange);margin-top:15px}
.post time{font-size:11px;color:var(--ink);display:block;margin-top:8px}

/* footer */
.site-footer{position:absolute;left:0;top:2675px;width:1200px;height:40px;background:var(--orange);display:flex;align-items:center;justify-content:space-between;padding:0 80px;color:var(--white);font-size:12px}
.social{display:flex;gap:8px}
.social span{width:26px;height:26px;border-radius:50%;border:2px solid var(--maroon)}
</style>
</head>
<body>

<header class="site-header">
  <div class="brand"><span class="brand-dot"></span><span class="brand-name">Top Whisker Tonic</span></div>
  <div class="avatar" role="img" aria-label="Portrait photo of Delvin Marsk"></div>
  <div class="signature">Delvin Marsk</div>
  <div class="contact contact-mail">
    <span class="ico"><svg width="18" height="14" viewBox="0 0 18 14"><rect x="1" y="1" width="16" height="12" fill="none" stroke="#6b0a0a" stroke-width="2"/><path d="M1 1l8 7 8-7" fill="none" stroke="#6b0a0a" stroke-width="2"/></svg></span>
    info@topwhiskertonic.net
  </div>
  <div class="contact contact-phone">
    <span class="ico"><svg width="18" height="18" viewBox="0 0 24 24"><path fill="#6b0a0a" d="M6.6 10.8a15 15 0 006.6 6.6l2.2-2.2c.3-.3.7-.4 1-.2 1.1.4 2.3.6 3.6.6.6 0 1 .4 1 1V20c0 .6-.4 1-1 1A17 17 0 013 4c0-.6.4-1 1-1h3.5c.6 0 1 .4 1 1 0 1.3.2 2.5.6 3.6.1.3 0 .7-.2 1z"/></svg></span>
    123-456-7890
  </div>
  <nav class="main-nav">
    <a class="active">Home</a><a>About</a><span class="sep"></span><a>Our Charter</a><span class="sep"></span><a>Beard Oil Review Methodology</a><span class="sep"></span><a>Blog</a>
  </nav>
</header>

<section class="hero" role="img" aria-label="Photo of a spiced citrus beard oil bottle on a light wooden shelf">
  <svg class="hero-arrow" style="left:20px" width="36" height="90" viewBox="0 0 36 90"><path d="M32 4L6 45l26 41" fill="none" stroke="#fff" stroke-width="4"/></svg>
  <h1 class="hero-title display">Curate, Review &amp; Grade<br>Then Present</h1>
  <div class="hero-btn">See Table</div>
  <svg class="hero-arrow" style="left:1146px" width="36" height="90" viewBox="0 0 36 90"><path d="M4 4l26 41L4 86" fill="none" stroke="#fff" stroke-width="4"/></svg>
</section>

<div class="page-backdrop" role="img" aria-label="Light grey pattern of drawn bearded faces"></div>

<main class="content">
  <h2 class="welcome-title display">Welcome To <span>Top Whisker Tonic</span></h2>
  <p class="welcome-text">We are a global business with the mission is to curate all available beard oils from around the world, review &amp; grade them &amp; present this curated collection to the users of the site. Our Target Audience are all grooming men. Lorem ipsum dolor sit amet, consectetuer adipiscing elit, sed diam nonummy nibh euismod tincidunt ut laoreet dolore magna aliquam erat volutpat. Ut wisi enim ad minim veniam, quis nostrud exerci tation ullamcorper susci. Ut wisi enim ad minim veniam, quis nostrud exerci tation ullamcorper susci</p>

  <div class="process">
    <svg width="1080" height="200" style="position:absolute;left:0;top:0">
      <path id="arcA" d="M230 92 Q340 150 480 75" fill="none" stroke="#6b0a0a" stroke-width="1.5" stroke-dasharray="2 4"/>
      <path id="arcB" d="M605 75 Q720 -10 860 60" fill="none" stroke="#6b0a0a" stroke-width="1.5" stroke-dasharray="2 4"/>
      <text font-family="Raleway, sans-serif" font-size="13" fill="#6b0a0a"><textPath href="#arcA" startOffset="18%">We curate all available beard oils</textPath></text>
      <text font-family="Raleway, sans-serif" font-size="13" fill="#6b0a0a"><textPath href="#arcB" startOffset="8%">Review &amp; Grade them &amp; Present</textPath></text>
    </svg>
    <div class="step" style="left:76px;top:0">
      <div class="circle"><svg width="44" height="44" viewBox="0 0 24 24"><circle cx="9" cy="9" r="4" fill="none" stroke="#6b0a0a" stroke-width="2.4"/><path d="M12 12l7 9M16 6v6M19 8v6" stroke="#6b0a0a" stroke-width="2.4" stroke-linecap="round"/></svg></div>
      <div class="label display">Curate</div>
    </div>
    <div class="step" style="left:449px;top:-20px">
      <div class="circle"><svg width="46" height="46" viewBox="0 0 24 24"><circle cx="12" cy="12" r="10" fill="#6b0a0a"/><path fill="#f7a400" d="M12 5l2 4.5 5 .4-3.8 3.2 1.2 4.9L12 15.3 7.6 18l1.2-4.9L5 9.9l5-.4z"/></svg></div>
      <div class="label display">Review &amp; Grade</div>
    </div>
    <div class="step" style="left:824px;top:0">
      <div class="circle"><svg width="46" height="46" viewBox="0 0 24 24"><rect x="2" y="3" width="20" height="16" rx="1" fill="none" stroke="#6b0a0a" stroke-width="2.2"/><path d="M2 7h20M12 18v-8M8 13l4-4 4 4" fill="none" stroke="#6b0a0a" stroke-width="2.2"/></svg></div>
      <div class="label display">Present</div>
    </div>
  </div>

  <section class="compare">
    <div class="compare-head">
      <h2 class="display">Comparision Table</h2>
      <div class="filter" style="left:354px"><b>ORIGIN ▾</b>USA</div>
      <div class="filter" style="left:488px"><b>BASE OIL ▾</b>Lorem Ipsum</div>
      <div class="filter" style="left:633px"><b>SCENT ▾</b>Lorem Ipsum</div>
    </div>

    <div class="compare-row">
      <div class="thumb" role="img" aria-label="Product photo of a beard oil bottle"></div>
      <div class="product-name">Quillmoor Field Blend</div>
      <div class="product-maker">by Tallowmere Goods</div>
      <div class="meta" style="left:132px;top:99px"><b>Origin:</b> USA</div>
      <div class="meta" style="left:231px;top:99px"><b>Base Oil:</b> Jojoba, Hempseed</div>
      <div class="meta" style="left:421px;top:99px"><b>Scent:</b> Spice Market</div>
      <div class="meta" style="left:132px;top:128px"><b>Aroma:</b> 7</div>
      <div class="meta" style="left:231px;top:128px"><b>Therapeutic Affect:</b> 5</div>
      <div class="meta" style="left:421px;top:128px"><b>Value:</b> 5</div>
      <div class="meta" style="left:515px;top:128px"><b>Over All:</b> 5</div>
      <div class="buy">Buy Now</div>
    </div>
    <div class="compare-row">
      <div class="thumb" role="img" aria-label="Product photo of a beard oil bottle"></div>
      <div class="product-name">Brackwell Mercantile Tobacco</div>
      <div class="product-maker">by Tallowmere Goods</div>
      <div class="meta" style="left:132px;top:99px"><b>Origin:</b> USA</div>
      <div class="meta" style="left:231px;top:99px"><b>Base Oil:</b> Jojoba, Hempseed</div>
      <div class="meta" style="left:421px;top:99px"><b>Scent:</b> Spice Market</div>
      <div class="meta" style="left:132px;top:128px"><b>Aroma:</b> 7</div>
      <div class="meta" style="left:231px;top:128px"><b>Therapeutic Affect:</b> 5</div>
      <div class="meta" style="left:421px;top:128px"><b>Value:</b> 5</div>
      <div class="meta" style="left:515px;top:128px"><b>Over All:</b> 5</div>
      <div class="buy">Buy Now</div>
    </div>
    <div class="compare-row">
      <div class="thumb" role="img" aria-label="Product photo of a beard oil bottle"></div>
      <div class="product-name">The Whiskered Fellow Original</div>
      <div class="product-maker">by Tallowmere Goods</div>
      <div class="meta" style="left:132px;top:99px"><b>Origin:</b> USA</div>
      <div class="meta" style="left:231px;top:99px"><b>Base Oil:</b> Jojoba, Hempseed</div>
      <div class="meta" style="left:421px;top:99px"><b>Scent:</b> Spice Market</div>
      <div class="meta" style="left:132px;top:128px"><b>Aroma:</b> 7</div>
      <div class="meta" style="left:231px;top:128px"><b>Therapeutic Affect:</b> 5</div>
      <div class="meta" style="left:421px;top:128px"><b>Value:</b> 5</div>
      <div class="meta" style="left:515px;top:128px"><b>Over All:</b> 5</div>
      <div class="buy">Buy Now</div>
    </div>
    <div class="compare-row">
      <div class="thumb" role="img" aria-label="Product photo of a beard oil bottle"></div>
      <div class="product-name">Emberlyn Spiced Citrus</div>
      <div class="product-maker">by Tallowmere Goods</div>
      <div class="meta" style="left:132px;top:99px"><b>Origin:</b> USA</div>
      <div class="meta" style="left:231px;top:99px"><b>Base Oil:</b> Jojoba, Hempseed</div>
      <div class="meta" style="left:421px;top:99px"><b>Scent:</b> Spice Market</div>
      <div class="meta" style="left:132px;top:128px"><b>Aroma:</b> 7</div>
      <div class="meta" style="left:231px;top:128px"><b>Therapeutic Affect:</b> 5</div>
      <div class="meta" style="left:421px;top:128px"><b>Value:</b> 5</div>
      <div class="meta" style="left:515px;top:128px"><b>Over All:</b> 5</div>
      <div class="buy">Buy Now</div>
    </div>
    <div class="compare-row">
      <div class="thumb" role="img" aria-label="Product photo of a beard oil bottle"></div>
      <div class="product-name">The Whiskered Fellow Original</div>
      <div class="product-maker">by Tallowmere Goods</div>
      <div class="meta" style="left:132px;top:99px"><b>Origin:</b> USA</div>
      <div class="meta" style="left:231px;top:99px"><b>Base Oil:</b> Jojoba, Hempseed</div>
      <div class="meta" style="left:421px;top:99px"><b>Scent:</b> Spice Market</div>
      <div class="meta" style="left:132px;top:128px"><b>Aroma:</b> 7</div>
      <div class="meta" style="left:231px;top:128px"><b>Therapeutic Affect:</b> 5</div>
      <div class="meta" style="left:421px;top:128px"><b>Value:</b> 5</div>
      <div class="meta" style="left:515px;top:128px"><b>Over All:</b> 5</div>
      <div class="buy">Buy Now</div>
    </div>
    <div class="compare-row">
      <div class="thumb" role="img" aria-label="Product photo of a beard oil bottle"></div>
      <div class="product-name">Brackwell Mercantile Tobacco</div>
      <div class="product-maker">by Tallowmere Goods</div>
      <div class="meta" style="left:132px;top:99px"><b>Origin:</b> USA</div>
      <div class="meta" style="left:231px;top:99px"><b>Base Oil:</b> Jojoba, Hempseed</div>
      <div class="meta" style="left:421px;top:99px"><b>Scent:</b> Spice Market</div>
      <div class="meta" style="left:132px;top:128px"><b>Aroma:</b> 7</div>
      <div class="meta" style="left:231px;top:128px"><b>Therapeutic Affect:</b> 5</div>
      <div class="meta" style="left:421px;top:128px"><b>Value:</b> 5</div>
      <div class="meta" style="left:515px;top:128px"><b>Over All:</b> 5</div>
      <div class="buy">Buy Now</div>
    </div>
    <div class="compare-row">
      <div class="thumb" role="img" aria-label="Product photo of a beard oil bottle"></div>
      <div class="product-name">Brackwell Mercantile Tobacco</div>
      <div class="product-maker">by Tallowmere Goods</div>
      <div class="meta" style="left:132px;top:99px"><b>Origin:</b> USA</div>
      <div class="meta" style="left:231px;top:99px"><b>Base Oil:</b> Jojoba, Hempseed</div>
      <div class="meta" style="left:421px;top:99px"><b>Scent:</b> Spice Market</div>
      <div class="meta" style="left:132px;top:128px"><b>Aroma:</b> 7</div>
      <div class="meta" style="left:231px;top:128px"><b>Therapeutic Affect:</b> 5</div>
      <div class="meta" style="left:421px;top:128px"><b>Value:</b> 5</div>
      <div class="meta" style="left:515px;top:128px"><b>Over All:</b> 5</div>
      <div class="buy">Buy Now</div>
    </div>
    <div class="compare-row" style="border-bottom:none">
      <div class="thumb" role="img" aria-label="Product photo of a beard oil bottle"></div>
      <div class="product-name">Brackwell Mercantile Tobacco</div>
      <div class="product-maker">by Tallowmere Goods</div>
      <div class="meta" style="left:132px;top:99px"><b>Origin:</b> USA</div>
      <div class="meta" style="left:231px;top:99px"><b>Base Oil:</b> Jojoba, Hempseed</div>
      <div class="meta" style="left:421px;top:99px"><b>Scent:</b> Spice Market</div>
      <div class="meta" style="left:132px;top:128px"><b>Aroma:</b> 7</div>
      <div class="meta" style="left:231px;top:128px"><b>Therapeutic Affect:</b> 5</div>
      <div class="meta" style="left:421px;top:128px"><b>Value:</b> 5</div>
      <div class="meta" style="left:515px;top:128px"><b>Over All:</b> 5</div>
      <div class="buy">Buy Now</div>
    </div>
    <div class="loading"><svg width="18" height="18" viewBox="0 0 24 24"><path d="M20 12a8 8 0 11-3-6.2M20 4v5h-5" fill="none" stroke="#fff" stroke-width="2.4"/></svg>Loading More...</div>
  </section>

  <aside class="newsletter">
    <h3 class="display">Get More Stuff Like This In Your InBox</h3>
    <p>Subscribe to our mailing list &amp; get interesting stuff &amp; updates.</p>
    <div class="field">Enter your email here</div>
    <div class="signup">SIGNUP NOW</div>
    <small>We respect your privacy and take protecting it seriously</small>
  </aside>

  <h3 class="blog-title display">Latest Blog</h3>
  <article class="post" style="top:952px">
    <div class="pic" role="img" aria-label="Blog photo of a bearded man beside a beard oil title card" style="background:linear-gradient(120deg,#4a4a4a,#9b9b9b 60%,#d8d8d8)"></div>
    <h4>How to Use Tilda's Beard Oil</h4><time>February 12, 2016</time>
  </article>
  <article class="post" style="top:1209px">
    <div class="pic" role="img" aria-label="Blog photo of herbs, oils and a mortar on a wooden table" style="background:linear-gradient(120deg,#8a6a3a,#c9a462 50%,#6f7f3e)"></div>
    <h4>How to Use Tilda's Beard Oil</h4><time>February 12, 2016</time>
  </article>
  <article class="post" style="top:1466px">
    <div class="pic" role="img" aria-label="Blog photo of a bearded man outdoors in warm sunlight" style="background:linear-gradient(120deg,#d9c9a5,#8a7352 55%,#3f3628)"></div>
    <h4>How to Use Tilda's Beard Oil</h4><time>February 12, 2016</time>
  </article>
  <article class="post" style="top:1723px">
    <div class="pic" role="img" aria-label="Blog photo of a man trimming his beard against a blue wall" style="background:linear-gradient(120deg,#a9c7d6,#6f98ad 55%,#c6d9e2)"></div>
    <h4>How to Use Tilda's Beard Oil</h4><time>February 12, 2016</time>
  </article>
</main>

<footer class="site-footer">
  <span>Copyright 2016 Top Whisker Tonic. All Rights Reserved.</span>
  <div class="social"><span></span><span></span><span></span><span></span></div>
</footer>

</body>
</html>
```